New Organic Skin Care Line Needs to Design a Product Label

***THE WINNER OF THIS PROJECT WILL MOST LIKELY BECOME THE EXCLUSIVE DESIGNER FOR OUR OTHER PRODUCT LABELS***

We need a label design for a new organic skin care product line called "Maple Dew Gala." This specific product is a 100% pure organic coconut oil. It's used for skin hydration, protection, and makeup removal.

Info to include on front label:

1. Logo: Maple Dew Gala (attached)
2. Product Name: Pure Coconut Oil (emphasize "organic" somewhere)
3. Slogan: Hydrate your skin and hair.
4. Size: 8 FL OZ 236mL

Attached is:

1. The brand logo "Maple Dew Gala" with a white background.
2. An image of the bottle we will use.
3. An image of the bottle with lines to show the size and placement of the label.
4. The brand logo "Maple Dew Gala" with a black background. (photoshop file)

What we need:

A simple mock up of the front side of the label on the bottle. We first want to know what it will look like on the bottle given the size and dimensions.

- We would like one label with a white background (including the logo with a white background).
- We would like a second label with a black background (including the logo with a black background, just need to make the black font white instead of black).

We can get a great idea of what to expect from the front side of the label so we will complete the back side once we identify a winner.
Updates

Apologies, but we are now using a different bottle. The previous one is now discontinued. Please view the two most recent images uploaded. One is an image of the new bottle by itself. The other is an image of that bottle with instructions. Please use your most recent designs on the new bottle. Feel free to make any modifications you see fit to compliment the new bottle shape. Added Friday, March 18, 2016

Reason: We are still working with the label company to finalize the size. Once the size is confirmed we will have to tweak labels based on finalized measurements.

Target Market(s)

Women, 18-70

Industry/Entity Type

Skin Care Product

Font styles to use
Decorative
Script

Requirements
Must have
• -"shabby sheek" and "cute" theme
• -soft organic feel
• -the ingredients are organic, pure, and natural. That should be an essence of the label.

```html
<!DOCTYPE html>
<html lang="en">
<head>
<meta charset="utf-8">
<title>Maple Dew Gala – Organic Pure Coconut Oil Labels</title>
<link rel="stylesheet" href="https://fonts.googleapis.com/css2?family=Cinzel:wght@400;700&family=Dancing+Script:wght@500&display=swap">
<style>
  :root {
    --canvas: #ffffff;
    --ink-dark: #000000;
    --ink-light: #ffffff;
    --rose: #dcb0c1;
    --rose-soft: #e8c6d3;
    --rose-deep: #cf9fb2;
    --accent: #e0126c;
    --coconut-husk: #8a5e38;
    --coconut-flesh: #f3efe6;
    --leaf: #4d9a36;
  }
  * { box-sizing: border-box; margin: 0; padding: 0; }
  html, body { width: 1200px; height: 1000px; overflow: hidden; background: var(--canvas); }
  .canvas { position: relative; width: 1200px; height: 1000px; background: var(--canvas); }

  .panel-dark { position: absolute; left: 0; top: 487px; width: 600px; height: 513px; background: var(--ink-dark); }

  .label {
    position: absolute; width: 404px; height: 487px;
    font-family: "Cinzel", serif; text-align: center;
  }
  .label--dark { background: var(--ink-dark); color: var(--ink-light); }
  .label--light { background: var(--ink-light); color: var(--ink-dark); }

  .label__floral-frame {
    position: absolute; inset: 0;
    border: 48px solid transparent;
    border-top-width: 44px; border-bottom-width: 46px;
    border-image: linear-gradient(135deg, var(--rose-soft), var(--rose) 35%, var(--rose-deep) 55%, var(--rose) 75%, var(--rose-soft)) 1;
  }

  .label__brand {
    position: absolute; left: 0; right: 0; top: 166px;
    font-size: 17px; letter-spacing: 4.6px; font-weight: 400; white-space: nowrap;
  }

  .label__coconut {
    position: absolute; left: 142px; top: 206px; width: 116px; height: 72px;
    border-radius: 45% 45% 38% 38%;
    background:
      radial-gradient(ellipse at 45% 50%, var(--coconut-flesh) 0%, rgba(243,239,230,0) 38%),
      radial-gradient(ellipse at 60% 40%, var(--coconut-husk) 0%, rgba(138,94,56,0.6) 50%, rgba(77,154,54,0.5) 80%, rgba(77,154,54,0) 100%);
  }

  .label__organic {
    position: absolute; left: 0; right: 0; top: 300px;
    font-size: 22px; font-weight: 700; font-variant: small-caps; letter-spacing: 1px;
  }
  .label__product {
    position: absolute; left: 0; right: 0; top: 324px;
    font-size: 22px; font-weight: 400; font-variant: small-caps; letter-spacing: 1px; white-space: nowrap;
  }
  .label__slogan {
    position: absolute; left: 0; right: 0; top: 370px;
    font-family: "Dancing Script", cursive; font-weight: 500; font-size: 21px; color: var(--accent);
  }
  .label__size {
    position: absolute; left: 0; right: 0; top: 404px;
    font-size: 12px; letter-spacing: 0.5px;
  }

  .label--hero-dark { left: 92px; top: 503px; }
  .label--hero-light { left: 708px; top: 503px; }

  .label--preview { transform-origin: top left; }
  .label--preview-dark { left: 215px; top: 183px; transform: scale(0.40, 0.36); }
  .label--preview-light { left: 838px; top: 181px; transform: scale(0.41, 0.37); }
</style>
</head>
<body>
<main class="canvas">

  <section class="label label--dark label--preview label--preview-dark">
    <div class="label__floral-frame" role="img" aria-label="Border of pale pink rose illustrations"></div>
    <p class="label__brand">Maple Dew Gala</p>
    <div class="label__coconut" role="img" aria-label="Illustration of split coconut on green leaves"></div>
    <h2 class="label__organic">Organic</h2>
    <p class="label__product">Pure Coconut Oil</p>
    <p class="label__slogan">Hydrate your skin and hair.</p>
    <p class="label__size">8 FL OZ 236mL</p>
  </section>

  <section class="label label--light label--preview label--preview-light">
    <div class="label__floral-frame" role="img" aria-label="Border of pale pink rose illustrations"></div>
    <p class="label__brand">Maple Dew Gala</p>
    <div class="label__coconut" role="img" aria-label="Illustration of split coconut on green leaves"></div>
    <h2 class="label__organic">Organic</h2>
    <p class="label__product">Pure Coconut Oil</p>
    <p class="label__slogan">Hydrate your skin and hair.</p>
    <p class="label__size">8 FL OZ 236mL</p>
  </section>

  <div class="panel-dark"></div>

  <section class="label label--dark label--hero-dark">
    <div class="label__floral-frame" role="img" aria-label="Border of pale pink rose illustrations"></div>
    <p class="label__brand">Maple Dew Gala</p>
    <div class="label__coconut" role="img" aria-label="Illustration of split coconut on green leaves"></div>
    <h2 class="label__organic">Organic</h2>
    <p class="label__product">Pure Coconut Oil</p>
    <p class="label__slogan">Hydrate your skin and hair.</p>
    <p class="label__size">8 FL OZ 236mL</p>
  </section>

  <section class="label label--light label--hero-light">
    <div class="label__floral-frame" role="img" aria-label="Border of pale pink rose illustrations"></div>
    <p class="label__brand">Maple Dew Gala</p>
    <div class="label__coconut" role="img" aria-label="Illustration of split coconut on green leaves"></div>
    <h2 class="label__organic">Organic</h2>
    <p class="label__product">Pure Coconut Oil</p>
    <p class="label__slogan">Hydrate your skin and hair.</p>
    <p class="label__size">8 FL OZ 236mL</p>
  </section>

</main>
</body>
</html>
```